Brightfen Business Card Redesign & Logo Update

We need to update our business cards to something more modern and fresh. Brightfen can provide the current color schemes and old design examples, but welcome creativity in helping us with this redesign. PLEASE NOTE that we no longer utilize the "tree" and/or "leaf" imagery in our branding. If able would apprecaite an update on the quality of our "words only" logo in Ai. / PNG formats too.

Target Market(s)

Investors, landowners, corporate partners, contractors

Industry/Entity Type

Environmental Restoration & Conservation

Contact Information for Business Card

Logo, persons name, title, mailing address, phone and email, website url

Font styles to use
Other font styles liked:
• Merriweather

Requirements
Nice to have
• Logo, persons name, title, mailing address, phone and email, website url, but open to ideams
Should not have
• No all back backgrounds

```html
<!DOCTYPE html>
<html lang="en">
<head>
<meta charset="utf-8">
<title>Brightfen Business Card</title>
<link rel="stylesheet" href="https://fonts.googleapis.com/css2?family=Merriweather:wght@400;700&display=swap">
<style>
  :root {
    --backdrop: #d4d5d8;
    --card-dark: #34352f;
    --card-light: #ffffff;
    --brand-orange: #f08a24;
    --brand-green: #138a43;
    --ink: #2e2e2e;
    --paper-text: #ffffff;
  }
  * { margin: 0; padding: 0; box-sizing: border-box; }
  html, body {
    width: 900px; height: 1200px; overflow: hidden;
    background: var(--backdrop);
  }
  .canvas { position: relative; width: 900px; height: 1200px; }
  .card {
    position: absolute; left: 122px; width: 657px; height: 375px;
    border-radius: 14px; overflow: hidden;
  }
  .card--front { top: 204px; background: var(--card-dark); }
  .card--back { top: 621px; background: var(--card-light); }

  .company-name {
    font-family: "Merriweather", serif;
    font-weight: 700;
    color: var(--brand-orange);
    line-height: 1.1; white-space: nowrap;
  }
  .company-line {
    font-family: "Merriweather", serif;
    font-weight: 400;
    text-transform: uppercase;
    line-height: 1.2; white-space: nowrap;
  }

  .front-identity {
    position: absolute; left: 0; right: 0; top: 128px; text-align: center;
  }
  .front-identity .company-name { font-size: 72px; }
  .front-identity .company-line {
    font-size: 16px; letter-spacing: 2.4px; color: var(--paper-text); margin-top: 14px;
  }

  .back-identity {
    position: absolute; left: 40px; width: 272px; top: 150px; text-align: center;
  }
  .back-identity .company-name { font-size: 44px; }
  .back-identity .company-line {
    font-size: 10.5px; letter-spacing: 1.4px; color: #1a1a1a; margin-top: 10px;
  }

  .divider {
    position: absolute; left: 327px; top: 100px; width: 1.5px; height: 176px;
    background: #222;
  }
  .contact {
    position: absolute; left: 353px; top: 97px;
    font-family: "Merriweather", serif; color: var(--ink);
  }
  .contact__name {
    font-size: 26px; font-weight: 700; color: var(--brand-orange);
    line-height: 1.2; white-space: nowrap;
  }
  .contact__name .surname { color: var(--brand-green); }
  .contact__title { font-size: 16px; line-height: 1.4; margin-top: 1px; }
  .contact__address { font-size: 17px; line-height: 24px; margin-top: 5px; white-space: nowrap; }
  .contact__lines { list-style: none; margin-top: 5px; }
  .contact__lines li {
    font-size: 16.5px; line-height: 24px; letter-spacing: 0.4px;
    display: flex; align-items: center; gap: 6px; white-space: nowrap;
  }
  .contact__lines svg { width: 14px; height: 14px; flex: none; }

  .social {
    position: absolute; left: 0; right: 0; top: 312px;
    display: flex; justify-content: center; gap: 13px;
  }
  .social__dot { width: 32px; height: 32px; border-radius: 50%; }
  .social__dot--green { background: var(--brand-green); }
  .social__dot--orange { background: var(--brand-orange); }
</style>
</head>
<body>
<main class="canvas">
  <section class="card card--front" aria-label="Card front">
    <div class="front-identity">
      <div class="company-name">Brightfen</div>
      <div class="company-line">Environmental Credit Company</div>
    </div>
  </section>

  <section class="card card--back" aria-label="Card back">
    <div class="back-identity">
      <div class="company-name">Brightfen</div>
      <div class="company-line">Environmental Credit Company</div>
    </div>
    <div class="divider"></div>
    <div class="contact">
      <div class="contact__name">DANA <span class="surname">REYES</span></div>
      <div class="contact__title">Director</div>
      <div class="contact__address">4810 County Road 88,<br>Lindale, TX 75771</div>
      <ul class="contact__lines">
        <li>
          <svg viewBox="0 0 24 24" aria-hidden="true"><path fill="#f08a24" d="M6.6 10.8a15.1 15.1 0 0 0 6.6 6.6l2.2-2.2a1 1 0 0 1 1-.25 11.4 11.4 0 0 0 3.6.57 1 1 0 0 1 1 1V20a1 1 0 0 1-1 1A17 17 0 0 1 3 4a1 1 0 0 1 1-1h3.5a1 1 0 0 1 1 1c0 1.25.2 2.450.57 3.57a1 1 0 0 1-.25 1z"/></svg>
          (903) 555-0147
        </li>
        <li>
          <svg viewBox="0 0 24 24" aria-hidden="true"><rect x="2" y="5" width="20" height="14" rx="1" fill="#f08a24"/><path d="M2.5 6l9.5 7 9.5-7" fill="none" stroke="#fff" stroke-width="1.6"/></svg>
          info@brightfencredits.com
        </li>
        <li>
          <svg viewBox="0 0 24 24" aria-hidden="true"><circle cx="12" cy="12" r="9" fill="none" stroke="#f08a24" stroke-width="2"/><path d="M3 12h18M12 3c3 3 3 15 0 18M12 3c-3 3-3 15 0 18" fill="none" stroke="#f08a24" stroke-width="1.6"/></svg>
          www.brightfencredits.com
        </li>
      </ul>
    </div>
    <div class="social" aria-label="Social media links">
      <span class="social__dot social__dot--green"></span>
      <span class="social__dot social__dot--orange"></span>
      <span class="social__dot social__dot--green"></span>
    </div>
  </section>
</main>
</body>
</html>
```